Icons for each step of my seven step process

Hi, I run a business coaching service for dentists. I have a 7 step process I take my clients through. I need to create an icon for each of my steps.
I also need to create an info graphic that relates these 7 steps in a process ie one leading to the other and then ending up back at the beginning.
I'm also looking to possibly add an 8th step and would like an icon for that too as well as an info graphic showing the 8 steps please.
From a style point of view I like the look of BrellikPath.com. My website will be clean looking and I'd like the icons to be clean looking as well. I'm happy for an array of colours to be used as well. I DO NOT want any icons with teeth or dental specific images. These icons should describe the process not the market.
I'd like the icon enclosed. I do like the rounded corners type of design often associated with apps but I'm open to other shapes as well.
I'd like the icons to have a professional feel but still look "cool and groovy"
The icons should not be numbered either please.
The seven / eight steps are:
1. Foundations
2. Building a high performance team
3. Operating Systems
4. Financial Systems
5. Case Acceptance (this is essentially a sales process - no shopping cart icons though please)
6. WOW customer service
7. Marketing
8. Creating Balance (not a yin yang please)
I'm happy if you need to abbreviate some of these points to a single word or two EG Team.
Many thanks,
Corin
Target Market(s)
Dentists
Industry/Entity Type
Shopping
Requirements
Must have
- Enclosed images for the icons but not necessarily for the infogrpahic.
Professional looking but still look cool / arty / groovy
Modern font.
Nice to have
- See BrellikPath.com for inspiration.
Should not have
- No illustrations of "shopping carts" for case acceptance and no illustrations of "yin yang's" for balance.
No old style fancy / flowery fonts.
No metallic type or reflective icons please.

```html
<!DOCTYPE html>
<html lang="en">
<head>
<meta charset="utf-8">
<title>Seven Step Process Cycle</title>
<link rel="stylesheet" href="https://fonts.googleapis.com/css2?family=Fredoka:wght@600&display=swap">
<style>
  :root {
    --ring-green: #009900;
    --icon-white: #ffffff;
    --page-bg: #ffffff;
  }
  html, body {
    margin: 0;
    padding: 0;
    width: 1200px;
    height: 1000px;
    overflow: hidden;
    background: var(--page-bg);
  }
  .process-cycle {
    display: block;
    width: 1200px;
    height: 1000px;
  }
  .cycle-ring { fill: none; stroke: var(--ring-green); stroke-width: 148; }
  .flow-arrow-line { fill: none; stroke: var(--icon-white); stroke-width: 5; }
  .flow-arrow-head, .step-icon { fill: var(--icon-white); }
  .step-icon-line { stroke: var(--icon-white); fill: none; }
  .gear-hole { fill: var(--ring-green); }
  .gear-hole-ring { fill: none; stroke: var(--ring-green); stroke-width: 2.5; }
  .wow-label {
    font-family: "Fredoka", sans-serif;
    font-weight: 600;
    font-size: 20px;
    fill: var(--ring-green);
  }
  .dollar-sign {
    font-family: "Fredoka", sans-serif;
    font-weight: 600;
    font-size: 92px;
    fill: var(--icon-white);
  }
</style>
</head>
<body>
<svg class="process-cycle" viewBox="0 0 1200 1000" role="img" aria-label="Seven step process cycle: foundations, team, operating systems, financial systems, case acceptance, WOW customer service, marketing and creating balance">
  <circle class="cycle-ring" cx="604" cy="499" r="314"/>

  <!-- flow arrows -->
  <g class="flow-arrows">
    <path class="flow-arrow-line" d="M433 235 Q462 214 498 203"/>
    <polygon class="flow-arrow-head" points="492,190 520,196 497,214"/>

    <path class="flow-arrow-line" d="M708 208 Q745 219 772 240"/>
    <polygon class="flow-arrow-head" points="760,248 790,255 778,228"/>

    <path class="flow-arrow-line" d="M890 367 Q908 398 916 432"/>
    <polygon class="flow-arrow-head" points="903,432 920,456 930,428"/>

    <path class="flow-arrow-line" d="M888 617 Q876 655 859 680"/>
    <polygon class="flow-arrow-head" points="850,670 844,699 870,687"/>

    <path class="flow-arrow-line" d="M697 790 Q665 805 630 809"/>
    <polygon class="flow-arrow-head" points="631,795 603,810 631,822"/>

    <path class="flow-arrow-line" d="M470 777 Q435 764 408 743"/>
    <polygon class="flow-arrow-head" points="418,735 390,728 401,754"/>

    <path class="flow-arrow-line" d="M316 615 Q300 580 299 548"/>
    <polygon class="flow-arrow-head" points="287,549 298,522 312,549"/>

    <path class="flow-arrow-line" d="M302 415 Q309 380 328 350"/>
    <polygon class="flow-arrow-head" points="314,342 338,328 334,356"/>
  </g>

  <!-- foundations: brick stack -->
  <g class="step step-foundations">
    <rect class="step-icon" x="587" y="153" width="40" height="19"/>
    <rect class="step-icon" x="566" y="175" width="39" height="19"/>
    <rect class="step-icon" x="608" y="175" width="39" height="19"/>
    <rect class="step-icon" x="546" y="197" width="38" height="20"/>
    <rect class="step-icon" x="587" y="197" width="39" height="20"/>
    <rect class="step-icon" x="629" y="197" width="39" height="20"/>
  </g>

  <!-- team -->
  <rect class="step-icon step-team" x="802" y="258" width="105" height="71" rx="10" role="img" aria-label="Group of three team members"/>

  <!-- operating systems: gears -->
  <g class="step step-operating">
    <circle class="step-icon-line" cx="898" cy="528" r="33" stroke-width="8" stroke-dasharray="3 4.5"/>
    <circle class="step-icon" cx="898" cy="528" r="30"/>
    <circle class="gear-hole-ring" cx="898" cy="528" r="8"/>
    <circle class="step-icon-line" cx="944" cy="563" r="20" stroke-width="6" stroke-dasharray="2.5 3.5"/>
    <circle class="step-icon" cx="944" cy="563" r="17"/>
    <circle class="gear-hole-ring" cx="944" cy="563" r="5"/>
  </g>

  <!-- financial systems -->
  <text class="dollar-sign" x="785" y="781" text-anchor="middle">$</text>

  <!-- case acceptance: tick -->
  <path class="step-icon" d="M490 810 L514 823 Q540 785 572 763 Q540 790 518 845 Z"/>

  <!-- wow customer service -->
  <g class="step step-wow">
    <path class="step-icon" d="M336 632 C375 632 386 655 386 665 C386 674 380 681 372 686 Q378 694 386 699 Q365 698 356 690 Q345 691 335 690 C305 690 289 675 289 660 C289 643 307 632 336 632 Z"/>
    <text class="wow-label" x="337" y="667" text-anchor="middle" transform="rotate(6 337 661)">wow</text>
  </g>

  <!-- marketing: star -->
  <polygon class="step-icon" points="292,431 303,458 332,460 310,478 317,506 292,491 268,506 275,478 254,460 282,458"/>

  <!-- creating balance: scales -->
  <g class="step step-balance">
    <polygon class="step-icon" points="379,233 383,245 375,245"/>
    <line class="step-icon-line" x1="379" y1="245" x2="379" y2="303" stroke-width="5"/>
    <line class="step-icon-line" x1="343" y1="253" x2="415" y2="253" stroke-width="4"/>
    <line class="step-icon-line" x1="343" y1="255" x2="375" y2="248" stroke-width="4"/>
    <line class="step-icon-line" x1="383" y1="248" x2="415" y2="255" stroke-width="4"/>
    <line class="step-icon-line" x1="343" y1="255" x2="331" y2="281" stroke-width="2"/>
    <line class="step-icon-line" x1="343" y1="255" x2="356" y2="281" stroke-width="2"/>
    <line class="step-icon-line" x1="414" y1="255" x2="401" y2="281" stroke-width="2"/>
    <line class="step-icon-line" x1="414" y1="255" x2="427" y2="281" stroke-width="2"/>
    <path class="step-icon" d="M330 281 H357 Q354 290 343 290 Q333 290 330 281 Z"/>
    <path class="step-icon" d="M400 281 H427 Q424 290 413 290 Q403 290 400 281 Z"/>
    <rect class="step-icon" x="352" y="303" width="53" height="6"/>
  </g>
</svg>
</body>
</html>
```